Website for software company "velora"

We need a website for our software company/startup named "velora". We are developing several products (currently 3 standard-software products) which are all in different sectors, but all our products are available for Laptops/PC/Mobile Phones/Tablets, ... We do also create custom software and support our customers with consulting to optimize their processes.
We already have a Logo which you can find in the attached files.
We are a young team of 4 members (two founders and 2 employees).

To get an idea of our products -> the first one is a planning software for healthcare organizations (eg. BlueHaven, firebrigade, pharmacy), the second one is a booking software for sport clubs and the third one is a competition software for sports hunting. You see very diverse. Include or ignore this info of our products as you like.

The design has to be a bootstrap 4 (or higher) design. We have licenced FontAwesome as iconset. Responsive design should come without saying.

• Starting page, product pages, news section, contact, team, services

```html
<!DOCTYPE html>
<html lang="en">
<head>
<meta charset="utf-8">
<title>Velora — Software</title>
<link rel="stylesheet" href="https://fonts.googleapis.com/css2?family=Barlow+Condensed:wght@500;600;700&family=Lato:wght@400;700&display=swap">
<style>
:root{
  --orange:#f47521;
  --orange-dark:#e2671a;
  --ink:#222222;
  --text:#444444;
  --muted:#8a8a8a;
  --line:#e2e2e2;
  --light:#f4f4f4;
  --white:#ffffff;
}
*{box-sizing:border-box;margin:0;padding:0}
html,body{width:1200px;height:3595px;overflow:hidden;background:var(--white)}
body{position:relative;font-family:'Lato',sans-serif;color:var(--text)}
.abs{position:absolute}
.head{font-family:'Barlow Condensed',sans-serif;font-weight:700;color:var(--ink);text-transform:uppercase;line-height:1}
.head em{font-style:normal;color:var(--orange)}
.rule{position:absolute;height:4px;background:var(--orange);border-radius:2px}
.btn-outline{position:absolute;display:flex;align-items:center;justify-content:center;gap:12px;border:2px solid var(--orange);border-radius:3px;background:var(--white);color:var(--ink);font-size:15px;text-transform:uppercase}
.mark{width:12px;height:12px;background:var(--orange);display:inline-block}
.photo{position:absolute}
.nowrap{white-space:nowrap}
/* header */
.topbar{left:458px;top:0;width:632px;height:31px;background:var(--orange);color:var(--white);font-size:15px}
.topbar::before{content:"";position:absolute;left:-22px;top:0;border-top:31px solid var(--orange);border-left:22px solid transparent}
.notch{left:497px;top:30px;border-top:12px solid var(--orange);border-left:9px solid transparent;border-right:9px solid transparent}
.topbar span{position:absolute;top:6px;display:flex;align-items:center;gap:8px}
.dot{width:12px;height:12px;border-radius:50%;background:var(--white);display:inline-block}
.logo{display:flex;align-items:center;gap:10px;font-family:'Barlow Condensed',sans-serif;font-weight:700;font-size:50px;color:var(--ink);letter-spacing:2px;text-transform:uppercase;line-height:1}
.logo i{width:18px;height:18px;background:var(--orange)}
.nav a{position:absolute;top:56px;font-size:15px;color:var(--ink);text-decoration:none}
.call{left:898px;top:45px;width:192px;height:40px;background:var(--orange);border-radius:3px;color:var(--white);font-weight:700;font-size:15px;display:flex;align-items:center;justify-content:center;gap:10px}
/* hero */
.hero-photo{left:0;top:98px;width:1200px;height:598px;background:linear-gradient(100deg,#8a7565 0%,#b9a493 30%,#7b7c85 55%,#3d4452 80%,#5a5f6a 100%)}
.hero-title{left:112px;top:252px;color:var(--white);font-size:46px;letter-spacing:2px}
.hero-big{left:110px;top:304px;color:var(--white);font-size:68px;letter-spacing:16px}
.hero-text{left:112px;top:374px;color:#f1ece7;font-size:15px;line-height:26px}
.hero-btn{left:113px;top:434px;width:159px;height:39px;background:var(--white);border-radius:2px;font-size:15px;color:var(--ink);display:flex;align-items:center;justify-content:center;text-transform:uppercase}
.slider i{position:absolute;top:634px;height:3px;width:34px;background:var(--white)}
/* software */
.soft-bg{left:0;top:696px;width:1200px;height:659px;background:linear-gradient(180deg,#efe9e4 0%,#f6f3f0 50%,#ece7e2 100%)}
.card{position:absolute;top:855px;width:313px;height:415px;background:var(--white);box-shadow:0 2px 10px rgba(0,0,0,.08)}
.card .photo{left:9px;top:10px;width:295px;height:209px}
.card .badge{position:absolute;left:124px;top:183px;width:66px;height:66px;border-radius:50%;background:var(--white);box-shadow:0 2px 8px rgba(0,0,0,.12);display:flex;align-items:center;justify-content:center}
.card h3{position:absolute;left:24px;top:256px;font-family:'Barlow Condensed',sans-serif;font-weight:600;font-size:21px;color:var(--orange)}
.card p{position:absolute;left:24px;top:286px;width:270px;font-size:15px;line-height:26px;color:var(--text)}
.card .btn-outline{left:25px;top:348px;width:160px;height:42px}
.arrow{position:absolute;top:1063px}
/* about */
.about-text{left:642px;top:1642px;font-size:15px;line-height:26px;white-space:nowrap}
/* blog */
.blog-bg{left:0;top:1970px;width:1200px;height:600px;background:var(--light)}
.blog-intro{left:120px;top:2186px;font-size:14.5px;line-height:23.3px;white-space:nowrap}
.post{position:absolute;top:2057px;height:427px;background:var(--white);box-shadow:0 2px 8px rgba(0,0,0,.06);overflow:hidden}
.post .photo{left:0;top:0;width:100%;height:236px}
.post .date{position:absolute;top:8px;width:39px;height:45px;background:var(--orange);color:var(--white);text-align:center;font-family:Georgia,serif;font-size:18px;line-height:20px;padding-top:4px}
.post .date small{display:block;font-family:'Lato',sans-serif;font-size:10px;line-height:12px}
.post h4{position:absolute;left:26px;top:256px;font-family:'Barlow Condensed',sans-serif;font-weight:600;font-size:21px;color:var(--orange)}
.post p{position:absolute;left:26px;top:288px;width:216px;font-size:15px;line-height:23.5px;text-align:justify}
.post .more{position:absolute;left:28px;top:393px;font-size:14px;color:var(--orange);display:flex;align-items:center;gap:8px}
/* contact */
.form-card{left:158px;top:2675px;width:460px;height:467px;background:var(--white);box-shadow:0 2px 14px rgba(0,0,0,.1)}
.field{position:absolute;left:33px;width:395px;height:49px;border:1px solid var(--line);font-size:14px;color:var(--muted);padding:14px 14px}
.field svg{position:absolute;right:16px;top:15px}
.submit{position:absolute;left:33px;top:385px;width:395px;height:43px;background:var(--orange);border-radius:3px;color:var(--white);font-size:15px;font-weight:700;display:flex;align-items:center;justify-content:center;gap:12px}
.submit .mark{background:var(--white)}
/* footer */
.footer{left:0;top:3251px;width:1200px;height:344px;background:var(--orange);color:var(--white)}
.footer .logo{color:var(--white)}
.footer .logo i{background:var(--white)}
.f-title{position:absolute;font-family:'Barlow Condensed',sans-serif;font-weight:600;font-size:19px;text-transform:uppercase}
.f-text{position:absolute;font-size:15px;line-height:26px}
.thumb{position:absolute;left:885px;width:65px;height:50px;background:linear-gradient(135deg,#dfe4ea,#8f9aa8);border:2px solid var(--white)}
.copy{position:absolute;left:0;top:3526px;width:1200px;height:69px;border-top:1px solid rgba(255,255,255,.45);color:var(--white);font-size:15px;text-align:center;line-height:62px}
</style>
</head>
<body>

<!-- header -->
<div class="abs topbar">
  <span style="left:78px"><svg width="16" height="12" viewBox="0 0 16 12"><rect x="1" y="1" width="14" height="10" fill="none" stroke="#fff" stroke-width="1.4"/><path d="M1 1l7 6 7-6" fill="none" stroke="#fff" stroke-width="1.4"/></svg>info@velora.com</span>
  <span style="left:270px"><svg width="14" height="16" viewBox="0 0 14 16"><circle cx="7" cy="5" r="4" fill="none" stroke="#fff" stroke-width="1.4"/><path d="M1 15c1-4 11-4 12 0" fill="none" stroke="#fff" stroke-width="1.4"/></svg>Quas Molestias Excepturi Sint</span>
  <span style="left:560px"><i class="dot" aria-label="Social link"></i></span>
  <span style="left:590px"><i class="dot" aria-label="Social link"></i></span>
  <span style="left:618px"><i class="dot" aria-label="Social link"></i></span>
</div>
<div class="abs notch"></div>
<div class="abs logo" style="left:110px;top:28px"><i></i>VELORA</div>
<nav class="nav">
  <a style="left:487px">Home</a>
  <a style="left:557px">About</a>
  <a style="left:628px">Our Software ⌄</a>
  <a style="left:748px">Blog ⌄</a>
  <a style="left:808px">Contact</a>
</nav>
<div class="abs call"><svg width="15" height="15" viewBox="0 0 24 24"><path fill="#fff" d="M6.6 10.8a15 15 0 006.6 6.6l2.2-2.2c.3-.3.7-.4 1-.2 1.1.4 2.3.6 3.6.6.6 0 1 .4 1 1V20c0 .6-.4 1-1 1A17 17 0 013 4c0-.6.4-1 1-1h3.5c.6 0 1 .4 1 1 0 1.3.2 2.5.6 3.6.1.3 0 .7-.2 1z"/></svg>+1(555) 010 2030</div>

<!-- hero -->
<div class="photo hero-photo" role="img" aria-label="Photo of two colleagues in an office looking at a tablet together"></div>
<div class="abs head hero-title">Welcome to</div>
<div class="abs head hero-big">Velora</div>
<p class="abs hero-text nowrap">Duis Aute Irure Dolor In Reprehen<br>derit In Voluptate Velit Esse Cillum Dolo</p>
<div class="abs hero-btn">Get Started</div>
<div class="slider"><i style="left:541px;background:var(--orange)"></i><i style="left:583px"></i><i style="left:625px"></i></div>

<!-- software -->
<div class="photo soft-bg" role="img" aria-label="Faint background photo of an office team"></div>
<h2 class="abs head" style="left:109px;top:782px;font-size:42px;color:var(--orange)">Our Software</h2>
<div class="rule" style="left:109px;top:830px;width:72px"></div>
<p class="abs nowrap" style="left:431px;top:778px;font-size:15px;line-height:26px;color:var(--text)">Duis Aute Irure Dolor In Reprehenderit In Voluptate Velit Esse Cillum Dolore Eu Fugiat<br>Nulla Pariatur. Excepteur Sint Occaecat Cupidatat Non Proident, Sunt In Culpa Qui Officia</p>

<svg class="arrow" style="left:46px" width="20" height="34" viewBox="0 0 20 34"><path d="M17 2L3 17l14 15" fill="none" stroke="#fff" stroke-width="3"/></svg>
<svg class="arrow" style="left:1134px" width="20" height="34" viewBox="0 0 20 34"><path d="M3 2l14 15L3 32" fill="none" stroke="#fff" stroke-width="3"/></svg>

<div class="card" style="left:100px">
  <div class="photo" role="img" aria-label="Photo of a nurse and a doctor at a desk" style="background:linear-gradient(135deg,#c7d4dc,#8fa7b5 60%,#dfe3e6)"></div>
  <div class="badge"><svg width="30" height="30" viewBox="0 0 30 30"><path d="M15 25s-9-6-9-12a5 5 0 019-3 5 5 0 019 3c0 6-9 12-9 12z" fill="none" stroke="#f47521" stroke-width="1.8"/></svg></div>
  <h3>Healthcare Organizations</h3>
  <p>Deserunt Mollit Anim Id Est Laborum Sed Ut Perspiciatis Unde Omnis Iste</p>
  <div class="btn-outline">Learn More <i class="mark"></i></div>
</div>
<div class="card" style="left:442px">
  <div class="photo" role="img" aria-label="Photo of a young footballer kicking a ball on a pitch" style="background:linear-gradient(180deg,#c9d6e2 0%,#aab8c4 45%,#6c9a3f 60%,#4f7d2b 100%)"></div>
  <div class="badge"><svg width="30" height="30" viewBox="0 0 30 30"><circle cx="17" cy="6" r="3" fill="none" stroke="#f47521" stroke-width="1.8"/><path d="M16 10l-4 7 5 3-2 7M12 17l-4 2" fill="none" stroke="#f47521" stroke-width="1.8"/></svg></div>
  <h3>Sport clubs</h3>
  <p>Deserunt Mollit Anim Id Est Laborum Sed Ut Perspiciatis Unde Omnis Iste</p>
  <div class="btn-outline">Learn More <i class="mark"></i></div>
</div>
<div class="card" style="left:785px">
  <div class="photo" role="img" aria-label="Photo of a shooter with ear protection aiming a shotgun" style="background:linear-gradient(180deg,#b8d2e0 0%,#8db06a 40%,#4d7a35 70%,#3a5c8a 100%)"></div>
  <div class="badge"><svg width="30" height="30" viewBox="0 0 30 30"><path d="M4 16c5-1 8-6 11-6s5 2 11 0c-3 5-7 8-12 8-4 0-6 3-6 6" fill="none" stroke="#f47521" stroke-width="1.8"/></svg></div>
  <h3>Sports Hunting</h3>
  <p>Deserunt Mollit Anim Id Est Laborum Sed Ut Perspiciatis Unde Omnis Iste</p>
  <div class="btn-outline">Learn More <i class="mark"></i></div>
</div>

<!-- about -->
<div class="photo" role="img" aria-label="Photo of a smiling businesswoman in an office" style="left:209px;top:1447px;width:373px;height:395px;background:linear-gradient(90deg,#dfe6ec 0%,#c3ced8 45%,#5a4b44 75%,#2a2628 100%)"></div>
<div class="photo" role="img" aria-label="Photo of three colleagues looking at a tablet" style="left:112px;top:1697px;width:307px;height:177px;background:linear-gradient(90deg,#e6eaee,#b9c3cc 50%,#4b5566);border-top:3px solid #fff;border-right:10px solid #fff"></div>
<h2 class="abs head" style="left:642px;top:1492px;font-size:42px">About <em>Us</em></h2>
<div class="abs nowrap" style="left:642px;top:1542px;font-family:'Barlow Condensed',sans-serif;font-weight:600;font-size:28px;line-height:36px;color:var(--ink)">Ab Illo Inventore Veritatis Et Quasi Archit<br>Ecto Beatae Vitae Dicta <span style="color:var(--orange)">Custom Software</span></div>
<div class="rule" style="left:642px;top:1621px;width:84px"></div>
<p class="abs about-text">Duis Aute Irure Dolor In Reprehenderit In Voluptate Velit Esse<br>Cillum Dolore Eu Fugiat Nulla Pariatur. Excepteur Sint Occaecat<br>Cupidatat Non Proident, Sunt In Culpa Qui Officia Deserunt<br>Mollit Anim Id Est Laborum"Sed Ut Perspiciatis Unde Omnis<br>Iste Natus Error Sit Voluptatem Accusantium Doloremque</p>
<div class="btn-outline" style="left:642px;top:1790px;width:160px;height:42px">Learn More <i class="mark"></i></div>

<!-- blog -->
<div class="abs blog-bg"></div>
<h2 class="abs head" style="left:114px;top:2116px;font-size:42px">Our <em>Blog</em></h2>
<div class="rule" style="left:120px;top:2164px;width:74px"></div>
<p class="abs blog-intro">Sed Do Eiusmod Tempor<br>Incididunt Ut Labore Et<br>Dolore Magna Aliqua. Ut<br>Enim Ad Minim Veniam, Quis<br>Nostrud Exercitation Ullamco<br>Laboris Nisi Ut Aliquip Ex Ea<br>Commodo Consequat. Duis</p>
<div class="abs" style="left:120px;top:2365px;width:158px;height:40px;background:var(--orange);border-radius:3px;color:#fff;font-weight:700;font-size:15px;display:flex;align-items:center;justify-content:center;gap:12px">SUBSCRIBE <i class="mark" style="background:#fff"></i></div>

<div class="post" style="left:352px;width:270px">
  <div class="photo" role="img" aria-label="Photo of a team meeting around a table with laptops" style="background:linear-gradient(135deg,#e9ecef,#a9b3bb 55%,#56606a)"></div>
  <div class="date" style="right:12px">01<small>MAR</small></div>
  <h4>Perspiciatis Unde</h4>
  <p>Magni Dolores Eos Qui Ratione Voluptatem Sequi Nesciunt. Neque Porro Quisquam Est, Qui Dolorem Ipsum Quia Dolor Sit</p>
  <div class="more">JANUARY 20 2022 <svg width="18" height="8" viewBox="0 0 18 8"><path d="M0 4h16M12 1l4 3-4 3" fill="none" stroke="#f47521" stroke-width="1.5"/></svg></div>
</div>
<div class="post" style="left:646px;width:271px">
  <div class="photo" role="img" aria-label="Photo of two colleagues discussing work at a laptop" style="background:linear-gradient(135deg,#dfe4ea,#9aa6b2 50%,#39414d)"></div>
  <div class="date" style="right:12px">11<small>MAR</small></div>
  <h4>Aliquam Quaerat</h4>
  <p>Magni Dolores Eos Qui Ratione Voluptatem Sequi Nesciunt. Neque Porro Quisquam Est, Qui Dolorem Ipsum Quia Dolor Sit</p>
  <div class="more">JANUARY 20 2022 <svg width="18" height="8" viewBox="0 0 18 8"><path d="M0 4h16M12 1l4 3-4 3" fill="none" stroke="#f47521" stroke-width="1.5"/></svg></div>
</div>
<div class="post" style="left:940px;width:260px">
  <div class="photo" role="img" aria-label="Photo of two colleagues looking at a laptop together" style="background:linear-gradient(135deg,#eef0f2,#b6bec6 50%,#6b5a52)"></div>
  <div class="date" style="right:2px">12<small>APR</small></div>
  <h4>Nulla Pariatur</h4>
  <p>Magni Dolores Eos Qui Ratione Voluptatem Sequi Nesciunt. Neque Porro Quisquam Est, Qui Dolorem Ipsum Quia Dolor Sit</p>
  <div class="more">JANUARY 20 2022 <svg width="18" height="8" viewBox="0 0 18 8"><path d="M0 4h16M12 1l4 3-4 3" fill="none" stroke="#f47521" stroke-width="1.5"/></svg></div>
</div>

<!-- contact -->
<div class="photo" role="img" aria-label="Faint dotted world map decoration" style="left:1030px;top:2655px;width:170px;height:505px;background:linear-gradient(180deg,#f2f2f2,#e7e7e7 50%,#f4f4f4)"></div>
<div class="photo" role="img" aria-label="Photo of a smiling woman with glasses working on a laptop" style="left:558px;top:2658px;width:472px;height:502px;background:linear-gradient(120deg,#eceae6 0%,#d8cfc4 40%,#b48f6a 60%,#8d949c 85%,#e6e8ea 100%)"></div>
<div class="abs form-card">
  <h2 class="head" style="position:absolute;left:0;width:460px;top:30px;text-align:center;font-size:42px">Contact <em>Us</em></h2>
  <p class="nowrap" style="position:absolute;left:0;width:460px;top:78px;text-align:center;font-size:15px;line-height:26px">Duis Aute Irure Dolor In Reprehenderit In Voluptate<br>Velit Esse Cillum Dolore Eu Fugiat Nulla</p>
  <div class="rule" style="left:192px;top:136px;width:74px"></div>
  <div class="field" style="top:160px">Name<svg width="16" height="18" viewBox="0 0 16 18"><circle cx="8" cy="5" r="4" fill="#f47521"/><path d="M1 17c0-5 14-5 14 0z" fill="#f47521"/></svg></div>
  <div class="field" style="top:218px">Email Address<svg width="18" height="14" viewBox="0 0 18 14"><rect x="1" y="1" width="16" height="12" fill="none" stroke="#f47521" stroke-width="1.6"/><path d="M1 1l8 7 8-7" fill="none" stroke="#f47521" stroke-width="1.6"/></svg></div>
  <div class="field" style="top:278px;height:93px">Type Your Message<svg width="16" height="20" viewBox="0 0 16 20"><rect x="1" y="1" width="13" height="17" fill="none" stroke="#f47521" stroke-width="1.6"/><path d="M4 6h7M4 10h7M4 14h4" stroke="#f47521" stroke-width="1.4"/></svg></div>
  <div class="submit">SUBMIT <i class="mark"></i></div>
</div>

<!-- footer -->
<div class="abs footer"></div>
<div class="abs logo" style="left:109px;top:3336px;color:#fff"><i style="background:#fff"></i>VELORA</div>
<p class="f-text nowrap" style="left:109px;top:3393px;color:#fff">Duis Aute Irure Dolor In<br>Reprehenderit In Voluptate Velit</p>
<div class="abs" style="left:110px;top:3474px;display:flex;gap:24px">
  <i class="dot" aria-label="Social link"></i><i class="dot" aria-label="Social link"></i><i class="dot" aria-label="Social link"></i>
</div>

<div class="f-title" style="left:392px;top:3334px;color:#fff">Quick Link</div>
<div class="f-text" style="left:393px;top:3370px;color:#fff">Home<br>About<br>Our Software<br>Blog<br>Contact</div>

<div class="f-title" style="left:598px;top:3336px;color:#fff">Contact Us</div>
<svg class="abs" style="left:598px;top:3378px" width="14" height="20" viewBox="0 0 14 20"><path d="M7 0a7 7 0 00-7 7c0 5 7 13 7 13s7-8 7-13a7 7 0 00-7-7z" fill="#fff"/><circle cx="7" cy="7" r="2.5" fill="#f47521"/></svg>
<div class="f-text nowrap" style="left:627px;top:3376px;color:#fff">1245 Deserunt Mollit Anim<br>ventore Veritatis</div>
<svg class="abs" style="left:597px;top:3436px" width="15" height="15" viewBox="0 0 24 24"><path fill="#fff" d="M6.6 10.8a15 15 0 006.6 6.6l2.2-2.2c.3-.3.7-.4 1-.2 1.1.4 2.3.6 3.6.6.6 0 1 .4 1 1V20c0 .6-.4 1-1 1A17 17 0 013 4c0-.6.4-1 1-1h3.5c.6 0 1 .4 1 1 0 1.3.2 2.5.6 3.6.1.3 0 .7-.2 1z"/></svg>
<div class="f-text" style="left:624px;top:3432px;color:#fff">+1(555) 010 2030</div>
<svg class="abs" style="left:597px;top:3476px" width="15" height="11" viewBox="0 0 16 12"><rect x="1" y="1" width="14" height="10" fill="#fff"/><path d="M1 1l7 6 7-6" fill="none" stroke="#f47521" stroke-width="1.4"/></svg>
<div class="f-text" style="left:624px;top:3468px;color:#fff">info@velora.com</div>

<div class="f-title" style="left:882px;top:3337px;color:#fff">Popular Post</div>
<div class="thumb" style="top:3376px" role="img" aria-label="Thumbnail photo of colleagues at work"></div>
<div class="abs" style="left:967px;top:3377px;color:#fff;font-size:14px;line-height:23px"><b style="font-family:'Barlow Condensed',sans-serif;font-size:16px">Duis Aute Irure</b><br>May 01, 2022</div>
<div class="thumb" style="top:3444px" role="img" aria-label="Thumbnail photo of colleagues at a laptop"></div>
<div class="abs" style="left:967px;top:3445px;color:#fff;font-size:14px;line-height:23px"><b style="font-family:'Barlow Condensed',sans-serif;font-size:16px">Duis Aute Irure</b><br>May 01, 2022</div>

<div class="copy">Copy Rights @ 2022 Velora All Rights Reserved</div>

</body>
</html>
```